Lanternfield Drinks business cards

We need a business card design for our new logo. The company is modern, progressive, professional, yet approachable. The key products are ready to drink bottles and cans of coffee based beverages.
These cards will be a critical part of the first impression made by our sales organization, business development team, and all external facing personnel.
Card can be a vertical or horizontal orientation.

Target Market(s)

Customers, suppliers, business partners

Industry/Entity Type

Business

Contact Information for Business Card

Business cards should feature Company Name and Logo.

Font styles to use
Serif

Colors

Designer to choose colors to be used in the design.

Requirements
Must have
• Strong readability of Name, phone #, mobile number and email address.
• Job title, website url, Street Address, and other details can be secondary level readability.
Nice to have
• High impact, simplistic quality design.
• Ok to utilize the 'H in the box' separate from the company name

```html
<!DOCTYPE html>
<html lang="en">
<head>
<meta charset="utf-8">
<title>Lanternfield Drinks – Business Cards</title>
<link href="https://fonts.googleapis.com/css2?family=Lato:wght@400;700&display=swap" rel="stylesheet">
<style>
  :root {
    --backdrop: #2b2b2d;
    --brand-orange: #f05a2b;
    --card-white: #ffffff;
    --text-light: #ffffff;
    --text-soft: #ffe6dc;
  }
  * { box-sizing: border-box; margin: 0; padding: 0; }
  html, body {
    width: 1200px; height: 900px; overflow: hidden;
    background: var(--backdrop);
    font-family: "Lato", Arial, sans-serif;
  }
  .stage {
    position: relative; width: 1200px; height: 900px;
    display: flex; align-items: center; justify-content: center; gap: 40px;
  }
  .card {
    width: 520px; height: 300px; border-radius: 22px;
    position: relative; overflow: hidden;
  }
  .card--front { background: var(--brand-orange); color: var(--text-light); }
  .card--back {
    background: var(--card-white);
    display: flex; align-items: center; justify-content: center;
  }
  .front-brand {
    position: absolute; left: 0; top: 0; width: 250px; height: 300px;
    display: flex; flex-direction: column; align-items: center; justify-content: center; gap: 14px;
  }
  .brand-square {
    width: 34px; height: 34px; border: 4px solid var(--text-light);
  }
  .brand-name {
    font-weight: 700; font-size: 24px; line-height: 1.15; text-align: center;
    letter-spacing: 0.5px;
  }
  .divider {
    position: absolute; left: 262px; top: 45px; width: 1.5px; height: 210px;
    background: rgba(255,255,255,0.85);
  }
  .contact {
    position: absolute; left: 286px; top: 52px; right: 20px;
  }
  .contact__name { font-weight: 700; font-size: 19px; letter-spacing: 0.5px; }
  .contact__title { font-size: 12px; letter-spacing: 0.8px; color: var(--text-soft); margin-bottom: 12px; }
  .contact__list { list-style: none; }
  .contact__item {
    display: flex; align-items: flex-start; gap: 8px;
    font-size: 13px; line-height: 17px;
  }
  .contact__item--address { margin-top: 6px; }
  .icon { width: 14px; height: 14px; flex: none; margin-top: 1.5px; }
  .back-brand {
    display: flex; align-items: center; gap: 16px; color: var(--brand-orange);
  }
  .back-brand .brand-square { border-color: var(--brand-orange); width: 44px; height: 44px; border-width: 5px; }
  .back-brand .brand-name { font-size: 38px; text-align: left; }
</style>
</head>
<body>
<main class="stage">
  <section class="card card--front" aria-label="Card front">
    <div class="front-brand">
      <div class="brand-square"></div>
      <div class="brand-name">Lanternfield<br>Drinks</div>
    </div>
    <div class="divider"></div>
    <div class="contact">
      <div class="contact__name">DANA WHITLOW</div>
      <div class="contact__title">MANAGING DIRECTOR</div>
      <ul class="contact__list">
        <li class="contact__item">
          <svg class="icon" viewBox="0 0 14 14"><circle cx="7" cy="7" r="7" fill="#fff"/><path d="M4.5 3.8l1.3-.3.7 1.8-.9.6a5 5 0 0 0 2.5 2.5l.6-.9 1.8.7-.3 1.3c-3.5.2-6-2.3-5.7-5.7z" fill="#f05a2b"/></svg>
          <span>888 555 0172</span>
        </li>
        <li class="contact__item">
          <svg class="icon" viewBox="0 0 14 14"><circle cx="7" cy="7" r="7" fill="#fff"/><rect x="5" y="3.5" width="4" height="7" rx="0.8" fill="#f05a2b"/></svg>
          <span>888 444 0391</span>
        </li>
        <li class="contact__item">
          <svg class="icon" viewBox="0 0 14 14"><circle cx="7" cy="7" r="7" fill="#fff"/><rect x="3.8" y="4.8" width="6.4" height="4.4" fill="#f05a2b"/><path d="M3.8 4.8L7 7.3l3.2-2.5" stroke="#fff" stroke-width="0.7" fill="none"/></svg>
          <span>hello@lanternfield.com</span>
        </li>
        <li class="contact__item">
          <svg class="icon" viewBox="0 0 14 14"><circle cx="7" cy="7" r="7" fill="#fff"/><circle cx="7" cy="7" r="3.2" stroke="#f05a2b" stroke-width="1" fill="none"/><path d="M3.8 7h6.4M7 3.8v6.4" stroke="#f05a2b" stroke-width="0.8"/></svg>
          <span>www.lanternfield.com</span>
        </li>
        <li class="contact__item contact__item--address">
          <svg class="icon" viewBox="0 0 14 14"><circle cx="7" cy="7" r="7" fill="#fff"/><path d="M7 3.3a2.6 2.6 0 0 1 2.6 2.6C9.6 7.8 7 10.7 7 10.7S4.4 7.8 4.4 5.9A2.6 2.6 0 0 1 7 3.3z" fill="#f05a2b"/><circle cx="7" cy="5.9" r="0.9" fill="#fff"/></svg>
          <span>421, Address line here,<br>Dummy Code, 45452<br>Country Name</span>
        </li>
      </ul>
    </div>
  </section>
  <section class="card card--back" aria-label="Card back">
    <div class="back-brand">
      <div class="brand-square"></div>
      <div class="brand-name">Lanternfield<br>Drinks</div>
    </div>
  </section>
</main>
</body>
</html>
```